Design a New Business Card for Our Company

We are looking for fresh, unique, and a modern business card that reflects our roots as digital marketing agency focused on SEM.

Industry/Entity Type

Marketing

Contact Information for Business Card

looking for very unique out of the box designs. clean and modern that compliments our logo

Requirements
Must have
• colors should match our logo
• Front should have name, address, email, and phone/fax of the person, phone/fax are the same number
• back should have our url

```html
<!DOCTYPE html>
<html lang="en">
<head>
<meta charset="utf-8">
<title>Clearwave Solutions Business Card</title>
<link rel="stylesheet" href="https://fonts.googleapis.com/css2?family=Montserrat:wght@500;600&family=Roboto:wght@400;500&display=swap">
<style>
  :root {
    --page-bg: #d9d4cd;
    --card-top: #f1efec;
    --card-bottom: #e3e0dc;
    --brand-blue: #3f6f9f;
    --band-blue: #3d6c9e;
    --band-line: #7b8590;
    --band-text: #e4d6c2;
    --divider: #c98a7a;
    --logo-ink: #4d6e94;
    --address-ink: #3e6a9c;
  }
  * { margin: 0; padding: 0; box-sizing: border-box; }
  html, body {
    width: 1200px;
    height: 970px;
    overflow: hidden;
    background: var(--page-bg);
  }
  .business-card {
    position: absolute;
    left: 100px;
    top: 201px;
    width: 1000px;
    height: 567px;
    background: linear-gradient(180deg, var(--card-top), var(--card-bottom));
    box-shadow: 0 14px 40px rgba(60, 50, 40, 0.25);
    overflow: hidden;
    font-family: "Roboto", Arial, sans-serif;
  }
  .brand {
    position: absolute;
    left: 67px;
    top: 92px;
    display: flex;
    align-items: center;
    gap: 26px;
    color: var(--logo-ink);
    font-family: "Montserrat", Arial, sans-serif;
    font-weight: 600;
  }
  .brand-mark {
    width: 96px;
    height: 96px;
    border-radius: 50%;
    background: var(--logo-ink);
  }
  .brand-name {
    font-size: 92px;
    line-height: 0.9;
    letter-spacing: -3px;
  }
  .brand-tagline {
    display: block;
    font-size: 28px;
    letter-spacing: 31px;
    line-height: 1;
    margin-top: 14px;
  }
  .band-rule {
    position: absolute;
    left: 0;
    width: 100%;
    height: 5px;
    background: var(--band-line);
  }
  .band-rule.top { top: 300px; }
  .band-rule.bottom { top: 502px; }
  .contact-band {
    position: absolute;
    left: 0;
    top: 307px;
    width: 100%;
    height: 192px;
    background: var(--band-blue);
    color: var(--band-text);
  }
  .person {
    position: absolute;
    left: 72px;
    top: 38px;
    display: flex;
    align-items: center;
    font-family: "Montserrat", Arial, sans-serif;
  }
  .person-name {
    font-size: 29px;
    font-weight: 600;
    padding-right: 10px;
    border-right: 2px solid var(--band-text);
  }
  .person-role {
    font-size: 24px;
    font-weight: 500;
    padding-left: 10px;
  }
  .contact-list {
    position: absolute;
    list-style: none;
    font-size: 29px;
  }
  .contact-list li {
    display: flex;
    align-items: center;
    gap: 8px;
    height: 37px;
  }
  .contact-list.left { left: 72px; top: 89px; }
  .contact-list.right { left: 525px; top: 52px; }
  .contact-list svg { width: 30px; height: 30px; flex: none; }
  .column-divider {
    position: absolute;
    left: 474px;
    top: 56px;
    width: 2px;
    height: 104px;
    background: var(--divider);
  }
  .address {
    position: absolute;
    left: 0;
    top: 522px;
    width: 100%;
    text-align: center;
    font-size: 27px;
    font-weight: 500;
    color: var(--address-ink);
  }
</style>
</head>
<body>
<svg width="0" height="0" style="position:absolute">
  <defs>
    <symbol id="icon-phone" viewBox="0 0 30 30">
      <rect width="30" height="30" rx="3" fill="#e4d6c2"/>
      <path d="M6 12c0-3 4-5 9-5s9 2 9 5v2h-5v-2h-8v2H6z" fill="#3d6c9e"/>
      <rect x="8" y="15" width="14" height="9" rx="2" fill="#3d6c9e"/>
      <circle cx="15" cy="19.5" r="2.5" fill="#e4d6c2"/>
    </symbol>
    <symbol id="icon-fax" viewBox="0 0 30 30">
      <rect width="30" height="30" rx="3" fill="#e4d6c2"/>
      <rect x="9" y="5" width="12" height="7" fill="#3d6c9e"/>
      <rect x="5" y="12" width="20" height="10" rx="2" fill="#3d6c9e"/>
      <rect x="9" y="19" width="12" height="6" fill="#3d6c9e" stroke="#e4d6c2" stroke-width="1.5"/>
    </symbol>
    <symbol id="icon-mail" viewBox="0 0 30 30">
      <rect width="30" height="30" rx="3" fill="#e4d6c2"/>
      <rect x="5" y="8" width="20" height="14" fill="none" stroke="#3d6c9e" stroke-width="2"/>
      <path d="M5 8l10 8 10-8M5 22l7-6M25 22l-7-6" fill="none" stroke="#3d6c9e" stroke-width="2"/>
    </symbol>
  </defs>
</svg>

<div class="business-card">
  <div class="brand">
    <span class="brand-mark"></span>
    <div>
      <span class="brand-name">clearwave</span>
      <span class="brand-tagline">SOLUTIONS</span>
    </div>
  </div>

  <div class="band-rule top"></div>
  <section class="contact-band">
    <div class="person">
      <span class="person-name">JOHN SMITH</span>
      <span class="person-role">Maneger</span>
    </div>
    <ul class="contact-list left">
      <li><svg><use href="#icon-phone"/></svg>123 456 7890</li>
      <li><svg><use href="#icon-fax"/></svg>123 456 7890</li>
    </ul>
    <div class="column-divider"></div>
    <ul class="contact-list right">
      <li><svg><use href="#icon-phone"/></svg>123 456 7890</li>
      <li><svg><use href="#icon-fax"/></svg>123 456 7890</li>
      <li><svg><use href="#icon-mail"/></svg>your@yourcompany.com</li>
    </ul>
  </section>
  <div class="band-rule bottom"></div>

  <p class="address">Your Address,2nd Ste, Maplecrest, Texas 1234</p>
</div>
</body>
</html>
```